Software allocation system needs a business card design

We need a business card designed for our software platform - www.tallivo.com.au

At the moment the logo and website is all black and white, we are happy for suggestions on implementing some colour throughout either the logo or business card.

Industry/Entity Type

Software

Font styles to use
Sans Serif

Colors

Designer to choose colors to be used in the design.

```html
<!DOCTYPE html>
<html lang="en">
<head>
<meta charset="utf-8">
<title>Tallivo Business Card</title>
<link rel="stylesheet" href="https://fonts.googleapis.com/css2?family=Jost:wght@300;400&display=swap">
<style>
  :root {
    --page-bg: #e9eceb;
    --card-teal: #a7d8db;
    --card-white: #ffffff;
    --band-blue: #2a8fc1;
    --brand-grey: #55585b;
    --heading-blue: #1d6a88;
    --detail-blue: #3b9dc6;
  }
  * { margin: 0; padding: 0; box-sizing: border-box; }
  html, body {
    width: 1200px;
    height: 900px;
    overflow: hidden;
    background: var(--page-bg);
    font-family: "Jost", sans-serif;
  }
  .stage {
    width: 1200px;
    height: 900px;
    display: flex;
    align-items: center;
    justify-content: center;
  }
  .business-card {
    position: relative;
    width: 840px;
    height: 480px;
    background: var(--card-teal);
    overflow: hidden;
    box-shadow: 0 10px 30px rgba(0, 0, 0, 0.15);
  }
  .card-shapes {
    position: absolute;
    inset: 0;
  }
  .brand {
    position: absolute;
    left: 62px;
    top: 118px;
    color: var(--brand-grey);
  }
  .brand-name {
    display: flex;
    align-items: center;
    gap: 18px;
    font-weight: 300;
    font-size: 64px;
    letter-spacing: 10px;
    line-height: 1;
  }
  .brand-dot {
    width: 22px;
    height: 22px;
    border-radius: 50%;
    background: var(--detail-blue);
  }
  .brand-tagline {
    margin-top: 16px;
    font-weight: 300;
    font-size: 15px;
    letter-spacing: 1.6px;
    text-transform: uppercase;
  }
  .contact {
    position: absolute;
    left: 440px;
    top: 318px;
  }
  .contact-heading {
    font-weight: 400;
    font-size: 28px;
    color: var(--heading-blue);
    margin-bottom: 8px;
  }
  .contact-line {
    font-weight: 300;
    font-size: 21px;
    line-height: 1.45;
    color: var(--detail-blue);
    font-style: normal;
  }
</style>
</head>
<body>
  <main class="stage">
    <article class="business-card">
      <svg class="card-shapes" width="840" height="480" viewBox="0 0 840 480" xmlns="http://www.w3.org/2000/svg">
        <polygon class="white-panel" points="230,480 400,290 840,290 840,480" fill="var(--card-white)"/>
        <polygon class="pattern-band" role="img" aria-label="Blue triangle pattern band"
                 points="0,330 300,330 430,220 840,220 840,290 400,290 230,480 0,480"
                 fill="var(--band-blue)"/>
      </svg>

      <header class="brand">
        <div class="brand-name"><span class="brand-dot"></span>TALLIVO</div>
        <p class="brand-tagline">Planning &amp; compliance for heavy industry</p>
      </header>

      <section class="contact">
        <h2 class="contact-heading">Contact Us</h2>
        <address class="contact-line">PO Box 218<br>Kellridge NSW 2093</address>
        <p class="contact-line">hello@tallivo.com.au</p>
      </section>
    </article>
  </main>
</body>
</html>
```